Verodex business card

Business card for sustainable investment company called "Verodex". Verodex is an exchange platform selling carbon credits between buyers and sellers. Carbon Credits are an environmental commodity for reducing global carbon emissions.

the card should obviously have our logo and the theme should be sustainability/environment mixed with a trading platform.

Contact Information for Business Card

Logo, Name, Title, Phone, Email

Colors
0054AA
0677BA
7BADD7
CADEEF
E8F1F8
0094D4
00A9DD
6FCCEA
C7EBF8
E9F6FB
00AB8E
00BBA5
67D7C9
C6EFE9
E9F9F6
59FF00
82FF00
B8FF75
E3FFCB
F4FFEA

```html
<!DOCTYPE html>
<html lang="en">
<head>
<meta charset="utf-8">
<title>Verodex business card</title>
<link rel="stylesheet" href="https://fonts.googleapis.com/css2?family=Lexend:wght@400;500;600;700&display=swap">
<style>
  :root {
    --backdrop: #8f9190;
    --paper: #eceded;
    --ink: #0c1838;
    --ink-soft: #1a2545;
    --leaf: #00AB8E;
    --lagoon: #00BBA5;
    --sea: #0094D4;
    --ocean: #0054AA;
    --deboss: #d9e6e3;
  }
  * { margin: 0; padding: 0; box-sizing: border-box; }
  html, body {
    width: 1200px; height: 1200px; overflow: hidden;
    background: var(--backdrop);
    font-family: "Lexend", sans-serif;
    color: var(--ink);
  }
  .card {
    position: absolute;
    left: 209px;
    width: 796px;
    height: 441px;
    background: var(--paper);
  }
  .card--front { top: 98px; }
  .card--back { top: 634px; display: flex; align-items: center; justify-content: center; }

  .holder { position: absolute; left: 52px; top: 55px; }
  .holder__name {
    font-size: 33px; font-weight: 700; letter-spacing: -0.4px; line-height: 1;
    background: linear-gradient(90deg, var(--lagoon), var(--ocean));
    -webkit-background-clip: text; background-clip: text; color: transparent;
  }
  .holder__title { margin-top: 9px; font-size: 20px; font-weight: 400; color: var(--ink-soft); }

  .office { position: absolute; left: 52px; top: 240px; }
  .office__label { font-size: 20px; font-weight: 600; line-height: 1.4; }
  .office__address { font-size: 20px; font-weight: 400; line-height: 1.4; }

  .contacts { position: absolute; left: 52px; top: 304px; list-style: none; }
  .contacts__item {
    display: flex; align-items: center; gap: 10px;
    height: 29.5px; font-size: 20px; font-weight: 400;
  }
  .contacts__icon { width: 16px; height: 16px; flex: none; }

  .deboss-name {
    position: absolute; left: 400px; top: 190px; width: 330px;
    text-align: center; font-size: 60px; font-weight: 700;
    color: var(--deboss); letter-spacing: 1px; line-height: 1;
  }

  .brand { display: flex; align-items: center; gap: 24px; }
  .brand__square { width: 64px; height: 64px; background: var(--leaf); }
  .brand__name { font-size: 64px; font-weight: 700; color: var(--ink); letter-spacing: 1px; line-height: 1; }
</style>
</head>
<body>
  <section class="card card--front">
    <div class="holder">
      <h1 class="holder__name">Mark Halden</h1>
      <p class="holder__title">Sales Representative</p>
    </div>

    <div class="deboss-name">VERODEX</div>

    <div class="office">
      <p class="office__label">Verodex Head Office</p>
      <p class="office__address">Budapest XIII. Fenyves utca 14.</p>
    </div>

    <ul class="contacts">
      <li class="contacts__item">
        <svg class="contacts__icon" viewBox="0 0 24 24" aria-hidden="true">
          <path fill="#0677BA" d="M6.6 10.8a15 15 0 0 0 6.6 6.6l2.2-2.2c.3-.3.7-.4 1-.2 1.1.4 2.3.6 3.6.6.6 0 1 .4 1 1V20c0 .6-.4 1-1 1A17 17 0 0 1 3 4c0-.6.4-1 1-1h3.5c.6 0 1 .4 1 1 0 1.3.2 2.5.6 3.6.1.3 0 .7-.2 1z"/>
          <path fill="none" stroke="#00AB8E" stroke-width="1.8" stroke-linecap="round" d="M14 3a7 7 0 0 1 7 7M14 6.5a3.5 3.5 0 0 1 3.5 3.5"/>
        </svg>
        <span>+36 30 555 0142</span>
      </li>
      <li class="contacts__item">
        <svg class="contacts__icon" viewBox="0 0 24 24" aria-hidden="true">
          <rect x="2" y="5" width="20" height="14" fill="#0677BA"/>
          <path d="M2 5l10 8 10-8" fill="none" stroke="#6FCCEA" stroke-width="1.8"/>
        </svg>
        <span>szerviz@verodex.com</span>
      </li>
      <li class="contacts__item">
        <svg class="contacts__icon" viewBox="0 0 24 24" aria-hidden="true">
          <circle cx="12" cy="12" r="10" fill="#00AB8E"/>
          <path d="M2 12h20M12 2v20M12 2c-3.5 3-3.5 17 0 20M12 2c3.5 3 3.5 17 0 20" fill="none" stroke="#E9F9F6" stroke-width="1.4"/>
        </svg>
        <span>www.verodex.com</span>
      </li>
    </ul>
  </section>

  <section class="card card--back">
    <div class="brand">
      <span class="brand__square"></span>
      <span class="brand__name">VERODEX</span>
    </div>
  </section>
</body>
</html>
```